The Lantern of Grace Customized for my Business

Hi! I am interested in getting some design ideas to take this Lantern of Grace and put a bit of branding of my business into it. Open to any and all designs, this is intended to put on a 20"x24" or 16"x20" canvas so I can have it in my office for team training purposes. I have included a picture of the wall this canvas will go on. Thank you!

```html
<!DOCTYPE html>
<html lang="en">
<head>
<meta charset="utf-8">
<title>The Lantern of Grace – Brookhaven</title>
<link href="https://fonts.googleapis.com/css2?family=Lato:ital,wght@0,400;0,700;0,900;1,400&display=swap" rel="stylesheet">
<style>
  :root{
    --backdrop:#cbc7c3;
    --paper:#ffffff;
    --brand-blue:#29abe2;
    --ink:#222226;
    --badge:#2b2b2f;
    --footer:#3d3d42;
    --white:#ffffff;
  }
  html,body{margin:0;padding:0;overflow:hidden;}
  body{background:var(--backdrop);font-family:'Lato',sans-serif;}
  .canvas{position:relative;width:746px;height:1200px;overflow:hidden;background:var(--backdrop);}
  .poster{position:absolute;left:13px;top:312px;width:720px;height:576px;display:block;}
  .paper{fill:var(--paper);}
  .top-band{fill:var(--brand-blue);}
  .pyramid{fill:none;stroke:var(--ink);stroke-width:5;stroke-linejoin:miter;}
  .tier-line{stroke:var(--ink);stroke-width:1.5;}
  .dots{stroke:var(--brand-blue);stroke-width:2.5;stroke-dasharray:0.1 6;stroke-linecap:round;}
  .pill{fill:var(--badge);}
  .pill-label{fill:var(--white);font-family:'Lato',sans-serif;font-weight:900;font-size:11px;letter-spacing:1px;text-anchor:middle;}
  .body-copy{fill:var(--ink);font-family:'Lato',sans-serif;font-size:12px;text-anchor:middle;}
  .trait-ring{fill:var(--badge);}
  .trait-core{fill:var(--badge);stroke:var(--white);stroke-width:1.5;}
  .trait-name{fill:var(--brand-blue);font-family:'Lato',sans-serif;font-size:10.5px;text-anchor:middle;}
  .trait-name.small{font-size:8px;}
  .trait-note{fill:var(--white);font-family:'Lato',sans-serif;font-style:italic;font-size:9.5px;text-anchor:middle;}
  .brand-mark{fill:var(--brand-blue);}
  .brand-name{fill:var(--ink);font-family:'Lato',sans-serif;font-weight:700;font-size:30px;text-anchor:middle;}
  .title-banner{fill:var(--brand-blue);}
  .title-inner{fill:none;stroke:var(--white);stroke-width:2;}
  .title-text{fill:var(--white);font-family:'Lato',sans-serif;font-weight:900;font-size:40px;letter-spacing:5px;text-anchor:middle;}
  .footer-band{fill:var(--footer);}
  .footer-url{fill:var(--white);font-family:'Lato',sans-serif;font-weight:700;font-size:21px;text-anchor:middle;}
</style>
</head>
<body>
<div class="canvas">
<svg class="poster" viewBox="178 175 1208 966" xmlns="http://www.w3.org/2000/svg" aria-label="The Lantern of Grace poster">
  <rect class="paper" x="178" y="175" width="1208" height="966"/>
  <rect class="top-band" x="178" y="175" width="1208" height="20"/>

  <g class="brand">
    <circle class="brand-mark" cx="333" cy="318" r="13"/>
    <text class="brand-name" x="333" y="375">brookhaven</text>
  </g>

  <polygon class="pyramid" points="782,305 1312,911 252,911"/>
  <line class="tier-line" x1="611" y1="500" x2="953" y2="500"/>
  <line class="tier-line" x1="527" y1="597" x2="1037" y2="597"/>
  <line class="tier-line" x1="438" y1="698" x2="1126" y2="698"/>
  <line class="tier-line" x1="349" y1="800" x2="1215" y2="800"/>

  <!-- tier 1 -->
  <rect class="pill" x="724" y="420" width="116" height="17" rx="8.5"/>
  <text class="pill-label" x="782" y="432">STEADY LIGHT</text>
  <text class="body-copy" y="458"><tspan x="782">Shine brightest when it matters</tspan><tspan x="782" dy="14">most. Find quiet joy in a hard</tspan><tspan x="782" dy="14">task.</tspan></text>

  <!-- tier 2 -->
  <line class="dots" x1="722" y1="520" x2="832" y2="520"/>
  <rect class="pill" x="667" y="512" width="54" height="17" rx="8.5"/>
  <text class="pill-label" x="694" y="524">CALM</text>
  <rect class="pill" x="834" y="512" width="76" height="17" rx="8.5"/>
  <text class="pill-label" x="872" y="524">COURAGE</text>
  <text class="body-copy" y="546"><tspan x="684">Stay settled and clear. Meet</tspan><tspan x="678" dy="14">each moment as it comes. Let</tspan><tspan x="646" dy="14">worry pass by.</tspan></text>
  <text class="body-copy" y="546"><tspan x="868">Act despite doubt. It grows from</tspan><tspan x="872" dy="14">careful preparation and keeping</tspan><tspan x="900" dy="14">each step in clear view.</tspan></text>

  <!-- tier 3 -->
  <line class="dots" x1="666" y1="620" x2="765" y2="620"/>
  <line class="dots" x1="829" y1="620" x2="927" y2="620"/>
  <rect class="pill" x="571" y="612" width="94" height="17" rx="8.5"/>
  <text class="pill-label" x="618" y="624">READINESS</text>
  <rect class="pill" x="767" y="612" width="60" height="17" rx="8.5"/>
  <text class="pill-label" x="797" y="624">CRAFT</text>
  <rect class="pill" x="929" y="612" width="60" height="17" rx="8.5"/>
  <text class="pill-label" x="959" y="624">UNITY</text>
  <text class="body-copy" y="646"><tspan x="610">Rested, fed and clear of mind.</tspan><tspan x="608" dy="14">Daily habits build the strength</tspan><tspan x="604" dy="14">to serve others well. Keep a</tspan><tspan x="590" dy="14">sensible pace each day.</tspan></text>
  <text class="body-copy" y="646"><tspan x="797">Learn the basics deeply and</tspan><tspan x="797" dy="14">practice until they become</tspan><tspan x="797" dy="14">second nature.</tspan></text>
  <text class="body-copy" y="646"><tspan x="965">Caring for the people beside</tspan><tspan x="971" dy="14">you. Willing to set aside</tspan><tspan x="978" dy="14">personal credit so the</tspan><tspan x="992" dy="14">whole group can grow.</tspan></text>

  <!-- tier 4 -->
  <line class="dots" x1="579" y1="721" x2="657" y2="721"/>
  <line class="dots" x1="755" y1="721" x2="825" y2="721"/>
  <line class="dots" x1="905" y1="721" x2="1003" y2="721"/>
  <rect class="pill" x="477" y="713" width="100" height="17" rx="8.5"/>
  <text class="pill-label" x="527" y="725">DISCIPLINE</text>
  <rect class="pill" x="659" y="713" width="94" height="17" rx="8.5"/>
  <text class="pill-label" x="706" y="725">AWARENESS</text>
  <rect class="pill" x="827" y="713" width="76" height="17" rx="8.5"/>
  <text class="pill-label" x="865" y="725">RESOLVE</text>
  <rect class="pill" x="1005" y="713" width="60" height="17" rx="8.5"/>
  <text class="pill-label" x="1035" y="725">FOCUS</text>
  <text class="body-copy" y="754"><tspan x="522">Choose habits that serve you and</tspan><tspan x="518" dy="14">keep feelings in balance. Sound</tspan><tspan x="512" dy="14">judgment grows from steady practice.</tspan></text>
  <text class="body-copy" y="746"><tspan x="706">Notice what is around you.</tspan><tspan x="706" dy="14">Listen first. Stay curious</tspan><tspan x="706" dy="14">and keep growing.</tspan></text>
  <text class="body-copy" y="746"><tspan x="865">Make clear choices and own</tspan><tspan x="865" dy="14">them with confidence.</tspan><tspan x="865" dy="14">Mistakes are lessons,</tspan><tspan x="865" dy="14">not endings.</tspan></text>
  <text class="body-copy" y="746"><tspan x="1036">Pick a clear aim and hold it</tspan><tspan x="1042" dy="14">steady. Set aside distractions</tspan><tspan x="1052" dy="14">and keep going when progress</tspan><tspan x="1120" dy="14">is slow.</tspan></text>

  <!-- tier 5 -->
  <line class="dots" x1="482" y1="821" x2="564" y2="821"/>
  <line class="dots" x1="651" y1="821" x2="757" y2="821"/>
  <line class="dots" x1="819" y1="821" x2="916" y2="821"/>
  <line class="dots" x1="1002" y1="821" x2="1095" y2="821"/>
  <rect class="pill" x="387" y="813" width="94" height="17" rx="8.5"/>
  <text class="pill-label" x="434" y="825">DILIGENCE</text>
  <rect class="pill" x="565" y="813" width="85" height="17" rx="8.5"/>
  <text class="pill-label" x="607" y="825">KINDNESS</text>
  <rect class="pill" x="758" y="813" width="60" height="17" rx="8.5"/>
  <text class="pill-label" x="788" y="825">TRUST</text>
  <rect class="pill" x="917" y="813" width="84" height="17" rx="8.5"/>
  <text class="pill-label" x="959" y="825">TEAMWORK</text>
  <rect class="pill" x="1096" y="813" width="68" height="17" rx="8.5"/>
  <text class="pill-label" x="1130" y="825">WARMTH</text>
  <text class="body-copy" y="847"><tspan x="428">Good work takes time and</tspan><tspan x="424" dy="14">care. Lasting results come</tspan><tspan x="420" dy="14">from steady effort and</tspan><tspan x="414" dy="14">thought.</tspan></text>
  <text class="body-copy" y="847"><tspan x="607">Grows from respect and patience.</tspan><tspan x="607" dy="14">Small acts of care add up over</tspan><tspan x="607" dy="14">time and strengthen every</tspan><tspan x="607" dy="14">bond we share.</tspan></text>
  <text class="body-copy" y="847"><tspan x="788">Earned slowly and kept with</tspan><tspan x="788" dy="14">care. Keep your word, and</tspan><tspan x="788" dy="14">honor others.</tspan></text>
  <text class="body-copy" y="847"><tspan x="959">Work well with every colleague.</tspan><tspan x="959" dy="14">Hear others before you speak.</tspan><tspan x="959" dy="14">Look for the best answer,</tspan><tspan x="959" dy="14">not the one that is yours.</tspan></text>
  <text class="body-copy" y="847"><tspan x="1134">Spreads to everyone you</tspan><tspan x="1140" dy="14">meet. Bring a kind heart to</tspan><tspan x="1146" dy="14">the work in front of you</tspan><tspan x="1154" dy="14">each day.</tspan></text>

  <!-- edge traits -->
  <g transform="translate(714,362)"><circle class="trait-ring" r="36"/><circle class="trait-core" r="31"/><text class="trait-name" y="-8">HOPE</text><text class="trait-note" y="8"><tspan x="0">looking</tspan><tspan x="0" dy="10">forward</tspan></text></g>
  <g transform="translate(849,362)"><circle class="trait-ring" r="36"/><circle class="trait-core" r="31"/><text class="trait-name" y="-8">PEACE</text><text class="trait-note" y="8"><tspan x="0">a quiet</tspan><tspan x="0" dy="10">mind</tspan></text></g>
  <g transform="translate(634,453)"><circle class="trait-ring" r="36"/><circle class="trait-core" r="31"/><text class="trait-name" y="-8">GRIT</text><text class="trait-note" y="6"><tspan x="0">steady</tspan><tspan x="0" dy="10">effort</tspan></text></g>
  <g transform="translate(929,453)"><circle class="trait-ring" r="36"/><circle class="trait-core" r="31"/><text class="trait-name" y="-8">CANDOR</text><text class="trait-note" y="4"><tspan x="0">plain</tspan><tspan x="0" dy="10">speech</tspan></text></g>
  <g transform="translate(550,548)"><circle class="trait-ring" r="36"/><circle class="trait-core" r="31"/><text class="trait-name" y="-8">WISDOM</text><text class="trait-note" y="6"><tspan x="0">clear</tspan><tspan x="0" dy="10">thinking</tspan></text></g>
  <g transform="translate(1012,548)"><circle class="trait-ring" r="36"/><circle class="trait-core" r="31"/><text class="trait-name" y="-5">HUMILITY</text><text class="trait-note" y="8"><tspan x="0">earns</tspan><tspan x="0" dy="10">respect</tspan></text></g>
  <g transform="translate(463,645)"><circle class="trait-ring" r="36"/><circle class="trait-core" r="31"/><text class="trait-name small" y="-9">FLEXIBILITY</text><text class="trait-note" y="3"><tspan x="0">ready for</tspan><tspan x="0" dy="10">change</tspan></text></g>
  <g transform="translate(1097,645)"><circle class="trait-ring" r="36"/><circle class="trait-core" r="31"/><text class="trait-name" y="-8">FAIRNESS</text><text class="trait-note" y="6"><tspan x="0">in word</tspan><tspan x="0" dy="10">and deed</tspan></text></g>
  <g transform="translate(382,740)"><circle class="trait-ring" r="36"/><circle class="trait-core" r="31"/><text class="trait-name" y="-6">DRIVE</text><text class="trait-note" y="9"><tspan x="0">for worthy</tspan><tspan x="0" dy="10">aims</tspan></text></g>
  <g transform="translate(1181,740)"><circle class="trait-ring" r="36"/><circle class="trait-core" r="31"/><text class="trait-name" y="-2">GRATITUDE</text><text class="trait-note" y="10">thanks freely</text></g>

  <!-- title -->
  <rect class="title-banner" x="270" y="957" width="1025" height="80" rx="40"/>
  <rect class="title-inner" x="278" y="963" width="1009" height="68" rx="34"/>
  <text class="title-text" x="783" y="1011">THE LANTERN OF GRACE</text>

  <!-- footer -->
  <path class="footer-band" d="M178 1118 Q782 1052 1386 1118 L1386 1141 L178 1141 Z"/>
  <text class="footer-url" x="782" y="1118">www.brookhavenwellness.com</text>
</svg>
</div>
</body>
</html>
```